Im want a website LIKE VRX's and FleetHollow.com's with product payment options like Trenzo's

I need a website LIKE VRX with a header made EXACTLY LIKE THAT OF FLEETHOLLOWS .

The front page photo should be like that of FLEETHOLLOW's webpage as well.

The name of the website will be called "M.K. (Caldera Key)".

We will be targeting ALL MARKETS in a small town in central Panama and charging businesses "listing fees" like a phone book does but also providing informational blogs, news, and other interesting activities.

THIS IS A MULTI PAGE WEBSITE

THIS IS WHERE VRX's website meets Brivelle/FleetHollow.

Once the layout is built I will tweak and modify, add information, and upload items for sale.

Here is a list of specific categories that should be listed out above the front page header image/search bar

-- Home -- News -- Travel -- Activities -- Shop & Dine -- Store -- More... --

These categories should be spread across the bottom of the page in three sections:

WHATS SO GREAT ABOUT (Caldera Key),
HAND PICKED TOURS
ACTIVITIES etc.

Also lets use www.Trenzo.example 's
"HOT DESTINATIONS"
"BEAT THE BEST PRICES IN CALDERA KEY"
"OCTOBERS INSIDER PICKS"
"TOP DESTINATIONS"
and spread them in four sections side-by-side near the bottom of the page.

Overall I would like to see the finished product to be something LIKE VRX's and FleetHollows.

WE NEED ONLINE PAYMENT OPTIONS LIKE BRIVELLE'S WEBSITE HAS

This will be a desktop website but should be very mobile friendly as well.

-rodmund

P.S. Good luck!

If it isn't already too late to change the website name, the name of the website should be "Caldera Key". Added Friday, October 9, 2015

What do you guys think the budget should be to win this? Added Saturday, October 10, 2015

www.palmorra.example is the most amazing simple site. Whoever can make me a replica with my specifications will win immediately!!!! Added Sunday, October 18, 2015

OMG www.palmorra.example is the bomb!So simple and elegant. Whoever can make me an EXACT REPLICA OF WWW.PALMORRA.EXAMPLE as my site with the specifications mentioned in my brief will take home the $825.00 immediately! Good luck amigos! Added Sunday, October 18, 2015

Does anybody know how to add recurring monthly billing options on this website? Added Sunday, October 18, 2015

ALL MARKETS

Product

Coded - Design and coding required

5+ page

• Coinvey payment options.
• I must be able to add and remove photos/text and video from the HTML files in the page.
• Be creative my friends, and may the odds be forever in your favor!
• I added some photos of a good layout for our page below.

```html
<!DOCTYPE html>
<html lang="en">
<head>
<meta charset="utf-8">
<title>Caldera Key — Travel, News &amp; Local Listings</title>
<link href="https://fonts.googleapis.com/css2?family=Roboto:wght@300;400;500;700&display=swap" rel="stylesheet">
<style>
:root{
  --orange:#f6ab32;
  --orange-dark:#e49620;
  --ink:#222222;
  --bar:#1f1f1f;
  --nav:#2c2c2c;
  --text:#444444;
  --muted:#8a8a8a;
  --line:#d9d9d9;
  --paper:#f4f4f4;
  --white:#ffffff;
  --teal:#6cc0bd;
}
*{box-sizing:border-box;margin:0;padding:0}
html,body{width:1200px;height:3564px;overflow:hidden}
body{position:relative;background:var(--paper);font-family:'Roboto',Arial,sans-serif;color:var(--text)}
.abs{position:absolute}
.ph{position:absolute;display:block;overflow:hidden}
.ph.rel{position:relative}

/* header */
.topbar{left:0;top:0;width:1200px;height:36px;background:var(--bar);color:#ddd;font-size:13px}
.topbar .contact{position:absolute;top:10px;display:flex;align-items:center;gap:8px}
.topbar .auth{position:absolute;right:100px;top:9px;display:flex;gap:8px;align-items:center;font-weight:500;font-size:13px}
.topbar .auth b{color:var(--orange)}
.mainnav{left:0;top:36px;width:1200px;height:31px;background:var(--nav)}
.mainnav ul{list-style:none;display:flex;position:absolute;left:240px;top:0}
.mainnav li{color:#eee;font-size:13px;padding:0 16px;line-height:31px}
.mainnav li.active{background:var(--orange)}
.cart{position:absolute;right:100px;top:4px;background:var(--orange);color:#fff;font-size:12px;font-weight:500;padding:4px 10px;display:flex;gap:6px;align-items:center}
.subnav{left:0;top:67px;width:1200px;height:28px;background:#e9e6df}
.subnav ul{list-style:none;display:flex;position:absolute;left:240px}
.subnav li{font-size:12.5px;color:#333;padding:0 20px;line-height:28px}
.subnav li.active{background:#d3cfc6}
.logo{left:100px;top:0;width:138px;height:100px;background:var(--orange);z-index:3;display:flex;flex-direction:column;align-items:center;justify-content:flex-end;padding-bottom:8px}
.logo .mark{width:44px;height:44px;border:3px solid #fff;margin-bottom:10px}
.logo span{color:#fff;font-size:14px;font-weight:500}

/* hero */
.hero{left:0;top:95px;width:1200px;height:595px;
  background:
    radial-gradient(ellipse 26% 38% at 60% 12%, rgba(255,246,200,.95), rgba(255,230,150,.35) 45%, transparent 75%),
    radial-gradient(ellipse 22% 30% at 40% 35%, rgba(240,220,140,.45), transparent 70%),
    radial-gradient(ellipse 10% 38% at 84% 52%, rgba(190,150,105,.55), rgba(120,90,60,.25) 55%, transparent 80%),
    radial-gradient(ellipse 60% 30% at 50% 100%, rgba(110,140,40,.75), transparent 75%),
    linear-gradient(90deg, #2a3514 0%, #4d5e22 12%, #7f8c3a 30%, #a7ad5c 52%, #7d8a38 70%, #4f5f22 86%, #27310f 100%);}
.hero-title{left:143px;top:257px;width:420px;height:52px;background:var(--orange);color:#fff;font-size:28px;line-height:52px;padding-left:20px}
.feature{left:143px;height:52px;background:rgba(20,20,20,.68);color:#fff;font-size:22px;display:flex;align-items:center;gap:14px;padding-left:10px}
.news{left:0;top:690px;width:1200px;height:54px;background:#262626}
.news h3{position:absolute;left:100px;top:10px;color:#fff;font-size:32px;font-weight:500;letter-spacing:1px}
.news p{position:absolute;left:207px;top:8px;width:893px;height:38px;background:#eee;border:1px solid #bbb;font-size:13px;color:#333;line-height:36px;padding-left:14px;white-space:nowrap;overflow:hidden}

/* top stories */
.tab{left:100px;top:803px;width:316px;height:45px;background:var(--orange);color:#fff;font-weight:700;font-size:16px;line-height:45px;padding-left:24px}
.story-head{left:100px;top:1038px;width:316px;font-size:27px;font-weight:300;color:#333;line-height:34px}
.story-list{left:100px;top:1115px;width:316px;list-style:none}
.story-list li{font-size:15px;color:#333;height:41px;line-height:40px;border-bottom:1px solid var(--line)}
.lead-cap{left:444px;top:1181px;width:656px;height:126px;background:rgba(238,236,230,.94);padding:20px 36px}
.lead-cap h4{font-size:27px;font-weight:300;color:#444}
.lead-cap p{font-size:12.5px;color:#777;margin-top:10px;line-height:19px}

/* section headings */
.sec-title{left:100px;width:1000px;height:60px}
.sec-title i{position:absolute;left:0;top:0;width:84px;height:8px;background:var(--orange)}
.sec-title h2{position:absolute;left:0;top:22px;font-size:32px;font-weight:500;color:#222;background:var(--paper);padding-right:22px;z-index:1}
.sec-title b{position:absolute;left:0;right:0;top:40px;height:8px;background:#d3d3d3}

/* featured video */
.vcap{height:43px;color:#222;font-size:16px;font-weight:700;padding-left:24px;display:flex;justify-content:space-between;padding-right:16px;align-items:center}
.vcap.grey{background:#d9d9d9}
.vcap.orange{background:var(--orange);color:#fff}
.vtext{list-style:none;margin-top:4px}
.vtext li{font-size:15px;color:#333;height:42px;line-height:42px;border-bottom:1px solid var(--line);white-space:nowrap}

/* newsletter */
.newsletter{left:0;top:1896px;width:1200px;height:238px;
  background:
    radial-gradient(ellipse 14% 60% at 86% 40%, rgba(140,105,75,.75), transparent 75%),
    radial-gradient(ellipse 40% 40% at 30% 100%, rgba(120,135,120,.5), transparent 75%),
    linear-gradient(180deg, rgba(30,40,55,.35), rgba(30,35,40,.55)),
    linear-gradient(90deg,#3f5466 0%,#5d7284 35%,#74807e 62%,#6b6358 80%,#3a322a 100%);}
.newsletter h2{position:absolute;left:96px;top:50px;color:#fff;font-size:31px;font-weight:500}
.newsletter .rule{position:absolute;left:360px;top:70px;width:740px;height:7px;background:#c8cbd0}
.newsletter p{position:absolute;left:100px;top:96px;color:#fff;font-size:15px}
.field{position:absolute;top:140px;height:48px;background:#fff;border:1px solid #ccc;font-size:12px;color:#555;padding-left:16px;line-height:46px}
.subscribe{position:absolute;left:840px;top:140px;width:260px;height:48px;background:var(--orange);color:#fff;font-size:19px;letter-spacing:1px;text-align:center;line-height:48px}

/* must watch */
.mv-cap{height:34px;background:#222;color:#fff;font-size:16px;line-height:34px;padding-left:14px;margin-top:10px}
.time{position:absolute;left:10px;bottom:8px;color:#fff;font-size:12px;display:flex;align-items:center;gap:6px}
.strip{position:absolute;left:0;right:0;bottom:0;height:34px;background:rgba(246,171,50,.55)}
.img-card{background:#fff}
.pill{position:absolute;left:14px;top:14px;background:#fff;border-radius:12px;font-size:10px;padding:4px 12px;color:#333}
.img-info{height:76px;background:#fff;position:relative;padding:16px 18px}
.img-info h4{font-size:17px;font-weight:500;color:#222}
.img-info p{font-size:10px;color:#999;margin-top:4px}
.more{position:absolute;right:18px;top:20px;width:80px;height:34px;border-radius:6px;background:var(--teal);color:#fff;font-size:10px;font-weight:700;text-align:center;line-height:34px}

/* shop & dine */
.dine{left:0;top:2965px;width:1200px;height:255px;background:var(--orange)}
.plate{position:absolute;top:28px;width:196px;height:196px;border-radius:50%;border:6px solid #fff;overflow:hidden}
.pizza{background:radial-gradient(circle at 50% 40%,#7a5630,#5a3c1c 75%);display:flex;flex-direction:column;align-items:center;justify-content:center;color:#fff;font-size:44px;font-weight:300;letter-spacing:2px;gap:6px}

/* footer */
.footer{left:0;top:3220px;width:1200px;height:296px;background:#1e1e1e;color:#bbb}
.footer h5{position:absolute;top:70px;color:#fff;font-size:12px;font-weight:700}
.footer ul{position:absolute;top:100px;list-style:none}
.footer li{font-size:11px;color:#888;line-height:29px}
.flogo{position:absolute;left:112px;top:78px}
.flogo .mark{width:52px;height:52px;border:3px solid var(--orange)}
.flogo span{display:block;color:var(--orange);font-size:13px;margin-top:8px}
.flogo p{width:230px;font-size:11px;color:#777;line-height:16px;margin-top:6px}
.social li{width:112px;height:24px;line-height:24px;margin-bottom:6px;color:#fff;padding-left:12px;font-size:11px}
.tweet{font-size:10px;color:#999;line-height:13px;margin-bottom:14px;white-space:nowrap}
.tweet b{color:#fff}
.tweet span{color:#6aa7e8}
.copy{left:0;top:3516px;width:1200px;height:48px;background:#111;color:#fff;font-size:11px;font-weight:700;line-height:48px;padding-left:100px}
</style>
</head>
<body>

<header>
  <div class="abs topbar">
    <div class="contact" style="left:262px">
      <svg width="18" height="13" viewBox="0 0 18 13"><rect x="1" y="1" width="16" height="11" fill="none" stroke="#fff" stroke-width="1.5"/><path d="M1 1l8 6 8-6" fill="none" stroke="#fff" stroke-width="1.5"/></svg>
      hello@calderakey.example</div>
    <div class="contact" style="left:494px">
      <svg width="14" height="14" viewBox="0 0 14 14"><path d="M3 1l3 3-2 2c1 2 2 3 4 4l2-2 3 3-2 2C6 13 1 8 1 3z" fill="#fff"/></svg>
      1800-555-0142</div>
    <div class="auth"><svg width="14" height="14" viewBox="0 0 14 14"><path d="M1 7h8M6 4l3 3-3 3M9 1h4v12H9" fill="none" stroke="#fff" stroke-width="1.5"/></svg><b>Login</b> / Sign Up</div>
  </div>
  <div class="abs logo"><div class="mark"></div><span>Caldera Key</span></div>
  <nav class="abs mainnav">
    <ul><li class="active">Home</li><li>Store</li><li>News</li><li>Activities</li><li>Travel</li><li>Shop &amp; Dine</li><li>More</li><li>Contact</li></ul>
    <div class="cart"><svg width="14" height="12" viewBox="0 0 14 12"><path d="M1 1h2l2 7h7l1-5H4" fill="none" stroke="#fff" stroke-width="1.4"/><circle cx="6" cy="10.5" r="1" fill="#fff"/><circle cx="11" cy="10.5" r="1" fill="#fff"/></svg>CART</div>
  </nav>
  <div class="abs subnav"><ul><li class="active">Home Page 1</li><li>Home Page 2</li><li>Home Page 3</li><li>Home Page 4</li><li>Home Page 5</li></ul></div>
</header>

<section>
  <div class="ph hero" role="img" aria-label="Smiling backpacker giving a thumbs up in a sunlit pine forest"></div>
  <div class="abs hero-title">Best For Travelling Website</div>
  <div class="abs feature" style="top:316px;width:249px"><svg width="32" height="32" viewBox="0 0 24 24"><path d="M12 2l3 7h7l-6 4.5 2.3 7.5L12 16.5 5.7 21 8 13.5 2 9h7z" fill="none" stroke="#fff" stroke-width="1.6"/></svg>Pacakge Post Type</div>
  <div class="abs feature" style="top:378px;width:396px"><svg width="32" height="32" viewBox="0 0 24 24"><path d="M12 2l3 7h7l-6 4.5 2.3 7.5L12 16.5 5.7 21 8 13.5 2 9h7z" fill="none" stroke="#fff" stroke-width="1.6"/></svg>Booking Form by Formwell</div>
  <div class="abs feature" style="top:440px;width:332px"><svg width="32" height="32" viewBox="0 0 24 24"><path d="M12 2l3 7h7l-6 4.5 2.3 7.5L12 16.5 5.7 21 8 13.5 2 9h7z" fill="none" stroke="#fff" stroke-width="1.6"/></svg>Package Discount Feature</div>
  <div class="abs feature" style="top:501px;width:320px"><svg width="32" height="32" viewBox="0 0 24 24"><path d="M12 2l3 7h7l-6 4.5 2.3 7.5L12 16.5 5.7 21 8 13.5 2 9h7z" fill="none" stroke="#fff" stroke-width="1.6"/></svg>Pakcage Filtering System</div>
  <div class="abs news"><h3>NEWS:</h3><p>The latest travel news on the most significant developments in the travel industry including news affecting travel agents, tour operators,</p></div>
</section>

<section>
  <div class="abs tab">Top Stories</div>
  <div class="ph" style="left:100px;top:848px;width:316px;height:169px;background:
    radial-gradient(ellipse 40% 30% at 40% 62%, rgba(230,235,240,.9), transparent 75%),
    linear-gradient(180deg,#7fb1e0 0%,#a9cbe9 38%,#d8e2ea 58%,#8b9aa4 72%,#4f6a72 84%,#2f5a6e 100%)" role="img" aria-label="Lakefront city skyline under a clear sky"></div>
  <h3 class="abs story-head">Lorem ipsum is simply dummy text</h3>
  <ul class="abs story-list"><li>Lorem Ipsum is simply dummy text</li><li>Contrary to popular belief</li><li>Lorem Ipsum is simply dummy text</li><li>Contrary to popular belief</li><li>Lorem Ipsum is simply dummy text</li></ul>
  <div class="ph" style="left:444px;top:803px;width:656px;height:504px;background:
    radial-gradient(ellipse 35% 22% at 30% 22%, rgba(40,70,30,.55), transparent 75%),
    radial-gradient(ellipse 30% 20% at 75% 25%, rgba(40,70,30,.45), transparent 75%),
    radial-gradient(ellipse 60% 18% at 60% 50%, rgba(60,210,215,.7), transparent 80%),
    linear-gradient(180deg,#4f9fe0 0%,#7cc2ea 28%,#9fd6e8 38%,#2dbcc6 46%,#1fa3b0 56%,#4d7e3c 66%,#7a7048 78%,#cfc7b4 88%,#e6e2d8 100%)" role="img" aria-label="Palm trees on a rocky shore above a turquoise sea"></div>
  <div class="abs lead-cap"><h4>Lorem ipsum is simply dummy text</h4><p>Contrary to popular belief, Lorem Ipsum is not simply random text. It has roots in a piece of classical Latin literature from 45 BC, making it over 2000 years old.</p></div>
</section>

<section>
  <div class="abs sec-title" style="top:1366px"><i></i><h2>Featured Video</h2><b></b></div>
  <div class="abs" style="left:100px;top:1452px;width:484px">
    <div class="ph rel" style="height:195px;background:
      radial-gradient(ellipse 18% 45% at 40% 55%, rgba(120,95,80,.7), transparent 75%),
      radial-gradient(ellipse 10% 60% at 72% 30%, rgba(80,80,85,.55), transparent 75%),
      linear-gradient(180deg,#cfd6dc 0%,#b9c2c9 50%,#9aa1a6 72%,#6b625a 100%)" role="img" aria-label="Couple sitting on a terrace with a landmark tower behind"></div>
    <div class="vcap grey">Lorem ipsum is simply dummy text<svg width="26" height="26" viewBox="0 0 26 26"><circle cx="13" cy="13" r="11" fill="none" stroke="#222" stroke-width="2"/><path d="M10 8l8 5-8 5z" fill="#222"/></svg></div>
    <ul class="vtext"><li>Lorem Ipsum is simply dummy text of the printing and typesetting</li><li>industry. Lorem Ipsum has been the industry's standard dummy text</li><li>ever since the 1500s, when an unknown printer took a galley of type</li><li>and scrambled it to make a type specimen book.</li></ul>
  </div>
  <div class="abs" style="left:615px;top:1452px;width:485px">
    <div class="ph rel" style="height:195px;background:
      radial-gradient(ellipse 16% 45% at 82% 55%, rgba(90,110,140,.7), transparent 75%),
      radial-gradient(ellipse 50% 18% at 35% 55%, rgba(70,100,110,.55), transparent 75%),
      linear-gradient(180deg,#b9d3e4 0%,#9fbfd2 35%,#6f93a2 55%,#4f6f5a 75%,#3f5a3a 100%)" role="img" aria-label="Two hikers resting on a ridge above a mountain valley"></div>
    <div class="vcap orange">Lorem ipsum is simply dummy text<svg width="26" height="26" viewBox="0 0 26 26"><circle cx="13" cy="13" r="11" fill="none" stroke="#fff" stroke-width="2"/><path d="M10 8l8 5-8 5z" fill="#fff"/></svg></div>
    <ul class="vtext"><li>Lorem Ipsum is simply dummy text of the printing and typesetting</li><li>industry. Lorem Ipsum has been the industry's standard dummy text</li><li>ever since the 1500s, when an unknown printer took a galley of type</li><li>and scrambled it to make a type specimen book.</li></ul>
  </div>
</section>

<section class="ph newsletter" role="img" aria-label="Travellers resting on a rock above a misty valley">
  <h2>Email Newsletter</h2><div class="rule"></div>
  <p>Join our newsletter and get the latest and hottest Hawaii travel deals.</p>
  <div class="field" style="left:100px;width:342px">Email</div>
  <div class="field" style="left:465px;width:342px">Zip Code</div>
  <div class="subscribe">Subscribe</div>
</section>

<section>
  <div class="abs sec-title" style="top:2206px"><i></i><h2>Must Watch Videos</h2><b></b></div>
  <div class="abs" style="left:100px;top:2283px;width:316px">
    <div class="ph rel" style="height:183px;background:
      radial-gradient(ellipse 22% 30% at 45% 50%, rgba(60,80,140,.7), transparent 75%),
      radial-gradient(ellipse 14% 28% at 80% 55%, rgba(200,60,70,.6), transparent 75%),
      linear-gradient(180deg,#5d6a4c 0%,#7b845c 40%,#6c6a52 70%,#8a7a58 100%)" role="img" aria-label="Family sitting in camp chairs beside a tent">
      <div class="strip"></div><span class="time"><svg width="12" height="12" viewBox="0 0 12 12"><circle cx="6" cy="6" r="5" fill="none" stroke="#fff"/><path d="M6 3v3h2" fill="none" stroke="#fff"/></svg>1:46</span></div>
    <div class="mv-cap">Lorem ipsum is simply dummy text</div>
  </div>
  <div class="abs" style="left:440px;top:2283px;width:318px">
    <div class="ph rel" style="height:183px;border:2px solid var(--orange);background:
      radial-gradient(ellipse 60% 25% at 50% 78%, rgba(30,60,40,.8), transparent 75%),
      linear-gradient(180deg,#3e4c44 0%,#4f7a78 45%,#3f8a8c 60%,#24463e 80%,#1d3028 100%)" role="img" aria-label="Row of palm trees on a beach at dusk">
      <svg class="abs" style="left:139px;top:54px" width="40" height="40" viewBox="0 0 40 40"><circle cx="20" cy="20" r="17" fill="none" stroke="#fff" stroke-width="3"/><path d="M16 12l11 8-11 8z" fill="#fff"/></svg>
      <span class="abs" style="left:0;width:314px;top:100px;text-align:center;color:#fff;font-size:13px">PLAY</span></div>
    <div class="mv-cap">Lorem ipsum is simply dummy text</div>
  </div>
  <div class="abs" style="left:782px;top:2283px;width:318px">
    <div class="ph rel" style="height:183px;background:
      radial-gradient(ellipse 35% 40% at 50% 45%, rgba(120,100,80,.8), transparent 75%),
      linear-gradient(180deg,#c9d6de 0%,#b5bfbf 25%,#8a7e68 50%,#6a6a48 75%,#4e5a34 100%)" role="img" aria-label="Ancient stone temple ruins among trees">
      <div class="strip"></div><span class="time"><svg width="12" height="12" viewBox="0 0 12 12"><circle cx="6" cy="6" r="5" fill="none" stroke="#fff"/><path d="M6 3v3h2" fill="none" stroke="#fff"/></svg>2:52</span></div>
    <div class="mv-cap">Lorem ipsum is simply dummy text</div>
  </div>
</section>

<section>
  <div class="abs sec-title" style="top:2566px"><i></i><h2>Must Watch Images</h2><b></b></div>
  <div class="abs img-card" style="left:100px;top:2642px;width:316px">
    <div class="ph rel" style="height:133px;background:
      radial-gradient(ellipse 40% 25% at 50% 60%, rgba(240,170,190,.7), transparent 75%),
      linear-gradient(180deg,#3c3a7a 0%,#6c5a9a 35%,#c08aa8 58%,#5a4060 72%,#2a2236 100%)" role="img" aria-label="Mountain range under a purple sunset sky"><span class="pill">MOUNTAIN</span></div>
    <div class="img-info"><h4>ALPS Mountains</h4><p>Lorem ipsum is simply dummy text of ...</p><span class="more">VIEW MORE</span></div>
  </div>
  <div class="abs img-card" style="left:442px;top:2642px;width:316px">
    <div class="ph rel" style="height:133px;background:
      radial-gradient(ellipse 60% 20% at 50% 8%, rgba(25,40,20,.9), transparent 80%),
      linear-gradient(180deg,#2c3a24 0%,#7aa8cc 30%,#b8d2e4 55%,#dfe8ee 68%,#5c9cc0 82%,#3a7aa0 100%)" role="img" aria-label="Tropical bay and distant hills framed by leaves"><span class="pill">MOUNTAIN</span></div>
    <div class="img-info"><h4>ALPS Mountains</h4><p>Lorem ipsum is simply dummy text of ...</p><span class="more">VIEW MORE</span></div>
  </div>
  <div class="abs img-card" style="left:784px;top:2642px;width:316px">
    <div class="ph rel" style="height:133px;background:
      radial-gradient(ellipse 30% 30% at 70% 30%, rgba(220,60,80,.7), transparent 75%),
      linear-gradient(180deg,#6a3a2c 0%,#b9705a 30%,#d8a07a 55%,#40a6cc 72%,#2a86b0 100%)" role="img" aria-label="Resort pool beneath flowering trees"><span class="pill">MOUNTAIN</span></div>
    <div class="img-info"><h4>ALPS Mountains</h4><p>Lorem ipsum is simply dummy text of ...</p><span class="more">VIEW MORE</span></div>
  </div>
</section>

<section>
  <div class="abs sec-title" style="top:2894px"><i></i><h2>Shop &amp; Dine</h2><b></b></div>
  <div class="abs dine">
    <div class="plate" style="left:119px;background:radial-gradient(circle at 50% 48%,#f0dcb0 0%,#d8a060 18%,#b85a30 32%,#f4efe8 46%,#e6e0d8 70%,#c9c2b8 100%)" role="img" aria-label="Plated pasta with sauce"></div>
    <div class="plate pizza" style="left:375px">PIZZA<svg width="30" height="20" viewBox="0 0 30 20"><path d="M2 10h24M18 3l8 7-8 7" fill="none" stroke="var(--orange)" stroke-width="2.5"/></svg></div>
    <div class="plate" style="left:632px;background:radial-gradient(circle at 50% 45%,#e0b070 0%,#a8552a 22%,#6a2e18 40%,#dcd4ca 58%,#b8aea2 100%)" role="img" aria-label="Grilled steak topped with garnish"></div>
    <div class="plate" style="left:889px;background:radial-gradient(circle at 50% 45%,#e8b050 0%,#b0702a 22%,#5a2e14 42%,#2a1a10 65%,#120c08 100%)" role="img" aria-label="Burger served on a dark table"></div>
  </div>
</section>

<footer>
  <div class="abs footer">
    <div class="flogo"><div class="mark"></div><span>Caldera Key</span>
      <p>Lorem ipsum is simply dummy text of the printing and typesetting industry. Lorem Ipsum has been the industry's standard dummy text ever since the 1500.</p></div>
    <h5 style="left:373px">FOLLOW US</h5>
    <ul class="social" style="left:373px"><li style="background:#3b5998">Friendloop</li><li style="background:#1da1f2">Chirper</li><li style="background:#dd4b39">Circlepost</li><li style="background:#cb2027">Pinstash</li></ul>
    <h5 style="left:539px">BEST TOURS</h5>
    <ul style="left:539px"><li>Camping holidays</li><li>Self-catering holidays</li><li>Safaris &amp; wildlife</li><li>Activities &amp; Adventures</li><li>Food &amp; wine holidays</li></ul>
    <h5 style="left:694px">POPULAR COUNTRIES</h5>
    <ul style="left:694px"><li>France</li><li>Ukraine</li><li>India</li><li>Spain</li><li>Turkey</li></ul>
    <ul style="left:770px"><li>Spain</li><li>Turkey</li><li>France</li><li>Ukraine</li><li>India</li></ul>
    <h5 style="left:879px">LATEST TWEETS</h5>
    <div class="abs" style="left:879px;top:100px;width:221px">
      <p class="tweet"><b>TrailhandCo</b> River tours <span>t.example/r8K2</span><br>@trailhand <span>t.example/Pq41</span></p>
      <p class="tweet"><b>TrailhandCo</b> Coffee walks <span>t.example/m3Lz</span><br>@trailhand <span>t.example/Xw90</span></p>
      <p class="tweet"><b>TrailhandCo</b> Market deals <span>t.example/Hd7c</span><br>@trailhand <span>t.example/Kt55</span></p>
    </div>
  </div>
  <div class="abs copy">COPYRIGHT © 2015 CALDERA KEY. ALL RIGHTS RESERVED.</div>
</footer>

</body>
</html>
```